Brantor Works Business Card

Modern and Professional Business Card for a Med size construction/development company.

See the samples below for the design I like … but I need ideas for incorporating the red company logo while still keeping the clean look of the card samples that are attached.

Logo and tag line on the back … info on the front.

Tagline: Solid Work Begins at the Footings

Target Market(s)

Med-Large General Contractors

Contact Information for Business Card

Brantor Works Limited
42 Fenwick Avenue
Harlow Cove, NL
A0X 2K7

t: 709-555-0147
f: 709-555-0182
w: www.brantorworks-example.com

Font styles to use
Sans Serif

Colors
fbee3e

Requirements
Must have
• I like the black and yellow designs of the attached samples …. but I'm not sure how to incorporate the red Brantor Works logo into that design??
Nice to have
• Construction safety strips

```html
<!DOCTYPE html>
<html lang="en">
<head>
<meta charset="utf-8">
<title>Brantor Works Business Card</title>
<link href="https://fonts.googleapis.com/css2?family=Montserrat:wght@400;600;800&display=swap" rel="stylesheet">
<style>
  :root {
    --backdrop: #3a3a3a;
    --card: #1c1c1c;
    --safety-yellow: #fbee3e;
    --brand-red: #e3202a;
    --ink-light: #f2f2f2;
    --ink-dark: #1a1a1a;
  }
  * { margin: 0; padding: 0; box-sizing: border-box; }
  html, body { width: 1200px; height: 1021px; overflow: hidden; }
  body {
    background: var(--backdrop);
    font-family: "Montserrat", sans-serif;
    position: relative;
  }
  .card {
    position: absolute;
    left: 250px;
    width: 700px;
    height: 400px;
    background: var(--card);
    box-shadow: 0 14px 30px rgba(0,0,0,.45);
    overflow: hidden;
  }
  .card--back { top: 60px; }
  .card--front { top: 560px; }

  .safety-strip {
    position: absolute;
    left: 0; right: 0;
    height: 26px;
    background: repeating-linear-gradient(115deg,
      var(--safety-yellow) 0 52px, transparent 52px 100px);
  }
  .card--back .safety-strip--top { top: 26px; }
  .card--back .safety-strip--bottom { bottom: 26px; }

  .brand-block {
    position: absolute;
    left: 0; right: 0;
    top: 128px;
    text-align: center;
  }
  .brand-name {
    font-weight: 800;
    font-size: 50px;
    letter-spacing: 1px;
    color: var(--brand-red);
    line-height: 1;
  }
  .brand-sub {
    font-weight: 800;
    font-size: 20px;
    letter-spacing: 6px;
    color: var(--brand-red);
    margin-top: 8px;
  }
  .tagline {
    margin-top: 22px;
    font-weight: 600;
    font-size: 17px;
    color: var(--ink-light);
  }

  .front-graphics { position: absolute; inset: 0; }
  .person {
    position: absolute;
    left: 90px;
    top: 140px;
    color: var(--ink-dark);
  }
  .person__name { font-weight: 800; font-size: 24px; line-height: 1.1; }
  .person__role { font-weight: 400; font-size: 16px; }

  .contact-list {
    position: absolute;
    left: 60px;
    top: 230px;
    list-style: none;
    color: var(--ink-light);
    font-size: 17px;
    line-height: 27px;
  }
  .contact-list li { display: flex; align-items: center; gap: 10px; }
  .contact-list svg { width: 15px; height: 15px; flex: none; }

  .front-brand {
    position: absolute;
    right: 40px;
    top: 50px;
    text-align: right;
  }
  .front-brand .brand-name { font-size: 40px; }
  .front-brand .brand-sub { font-size: 16px; letter-spacing: 5px; margin-top: 6px; }

  .address {
    position: absolute;
    right: 50px;
    top: 262px;
    text-align: right;
    color: var(--ink-light);
    font-size: 17px;
    line-height: 26px;
    font-style: normal;
  }
</style>
</head>
<body>

  <section class="card card--back" aria-label="Card back">
    <div class="safety-strip safety-strip--top"></div>
    <div class="brand-block">
      <div class="brand-name">BRANTOR WORKS</div>
      <div class="brand-sub">LIMITED</div>
      <div class="tagline">Solid Work Begins at the Footings</div>
    </div>
    <div class="safety-strip safety-strip--bottom"></div>
  </section>

  <section class="card card--front" aria-label="Card front">
    <svg class="front-graphics" viewBox="0 0 700 400" width="700" height="400" aria-hidden="true">
      <polygon points="0,130 390,130 420,200 0,200" fill="var(--safety-yellow)"/>
      <g fill="var(--safety-yellow)">
        <polygon points="440,172 490,172 478,200 428,200"/>
        <polygon points="512,172 562,172 550,200 500,200"/>
        <polygon points="584,172 634,172 622,200 572,200"/>
        <polygon points="656,172 706,172 694,200 644,200"/>
      </g>
    </svg>

    <div class="person">
      <div class="person__name">Daniel Whitcombe</div>
      <div class="person__role">Founder / Owner</div>
    </div>

    <ul class="contact-list">
      <li>
        <svg viewBox="0 0 16 16"><path d="M3 1l3 3-2 2c1 2 3 4 5 5l2-2 3 3-2 3C6 15 1 10 2 3z" fill="var(--safety-yellow)"/></svg>
        709-555-0147
      </li>
      <li>
        <svg viewBox="0 0 16 16"><rect x="4" y="1" width="8" height="4" fill="var(--safety-yellow)"/><rect x="1" y="6" width="14" height="6" rx="1" fill="var(--safety-yellow)"/><rect x="4" y="10" width="8" height="5" fill="var(--safety-yellow)"/></svg>
        709-555-0182
      </li>
      <li>
        <svg viewBox="0 0 16 16"><rect x="1" y="3" width="14" height="10" fill="none" stroke="var(--safety-yellow)" stroke-width="1.6"/><path d="M1 3l7 6 7-6" fill="none" stroke="var(--safety-yellow)" stroke-width="1.6"/></svg>
        info@brantorworks-example.com
      </li>
      <li>
        <svg viewBox="0 0 16 16"><circle cx="8" cy="8" r="6.5" fill="none" stroke="var(--safety-yellow)" stroke-width="1.4"/><path d="M1.5 8h13M8 1.5c-3 3-3 10 0 13M8 1.5c3 3 3 10 0 13" fill="none" stroke="var(--safety-yellow)" stroke-width="1.2"/></svg>
        www.brantorworks-example.com
      </li>
    </ul>

    <div class="front-brand">
      <div class="brand-name">BRANTOR WORKS</div>
      <div class="brand-sub">LIMITED</div>
    </div>

    <address class="address">
      Brantor Works Limited<br>
      42 Fenwick Avenue<br>
      Harlow Cove, NL<br>
      A0X 2K7
    </address>
  </section>

</body>
</html>
```